real esate business card with company logo and name

we need a business card design for a real esate company

The company name is Walsh & Brand Pty Ltd, and we have our logo designed and will upload. We want classic or moden feel. Black or white background. looks more textured. Should include folowinginformations
Owen Walsh and Lucy Brand
Sales Agents & Onsite Manager
p: 07 5948 2063
F: 07 5948 2174
M:0431 857 219
3/42 Marlow Crescent, FERNLEA QLD 4213

We want this business card looks professonal. Thank you in advance.

Industry/Entity Type

Real Estate Agent

Contact Information for Business Card

Owen Walsh and Lucy Brand
Onsite Manager & Sales Agents
p: 07 5948 2063
M:0431 857 219

Font styles to use
Serif

Colors
000000
fbfbfb
333333
959595

Requirements
Must have
• company logo and name, black or white back ground

```html
<!DOCTYPE html>
<html lang="en">
<head>
<meta charset="utf-8">
<title>Walsh &amp; Brand Pty Ltd — Business Card</title>
<link rel="stylesheet" href="https://fonts.googleapis.com/css2?family=Cormorant+SC:wght@400;500&family=Cormorant+Garamond:wght@400;500&family=Josefin+Sans:wght@400&display=swap">
<style>
  :root {
    --black: #000000;
    --ink: #333333;
    --mid: #959595;
    --paper: #fbfbfb;
    --silver: #cfcfcf;
    --stage: #e9e7e4;
    --serif-sc: "Cormorant SC", "Cormorant Garamond", serif;
    --serif: "Cormorant Garamond", serif;
    --brand: "Josefin Sans", sans-serif;
  }
  * { box-sizing: border-box; margin: 0; padding: 0; }
  html, body { width: 1200px; height: 913px; overflow: hidden; }
  body { background: var(--stage); position: relative; }

  .card {
    position: absolute;
    width: 560px;
    height: 320px;
    border-radius: 3px;
    box-shadow: 0 14px 30px rgba(0,0,0,.28);
    overflow: hidden;
  }

  /* Front: dark brushed finish */
  .card-front {
    left: 60px; top: 110px;
    background:
      repeating-linear-gradient(90deg, rgba(255,255,255,.025) 0 1px, transparent 1px 3px),
      linear-gradient(160deg, #4a4a4a 0%, var(--ink) 35%, #1a1a1a 70%, var(--black) 100%);
    color: var(--paper);
  }
  .front-band {
    position: absolute; right: 0; bottom: 0;
    width: 34%; height: 20%;
    background: linear-gradient(180deg, #b3b3b3, var(--mid));
  }
  .brand-mark {
    position: absolute; left: 40px; top: 92px;
    display: flex; align-items: center; gap: 12px;
  }
  .brand-square {
    width: 26px; height: 26px; background: var(--mid);
  }
  .brand-name {
    font-family: var(--brand);
    font-size: 13px; letter-spacing: 1.5px;
    text-transform: uppercase; color: var(--mid);
  }
  .agent-block {
    position: absolute; right: 34px; top: 58px; text-align: right;
  }
  .agent-names {
    font-family: var(--serif-sc);
    font-size: 25px; font-weight: 500; letter-spacing: .5px;
  }
  .agent-role {
    font-family: var(--serif-sc);
    font-size: 14px; color: var(--mid); letter-spacing: .5px;
  }
  .rule {
    position: absolute; height: 1px; background: var(--mid);
  }
  .rule-name { right: 34px; top: 126px; width: 400px; }
  .rule-contact { left: 40px; top: 196px; width: 170px; }
  .contact-list {
    position: absolute; left: 40px; top: 206px; list-style: none;
    font-family: var(--serif); font-size: 15px; line-height: 22px; color: var(--paper);
  }
  .contact-list li { display: flex; align-items: center; gap: 8px; }
  .contact-list svg { width: 12px; height: 12px; fill: var(--mid); }
  .address {
    position: absolute; right: 34px; top: 170px; text-align: right;
    font-family: var(--serif-sc); font-size: 16px; line-height: 22px;
  }

  /* Back: pale textured finish */
  .card-back {
    left: 590px; top: 480px;
    background:
      radial-gradient(circle at 30% 70%, rgba(255,255,255,.7), transparent 55%),
      linear-gradient(150deg, var(--paper) 0%, #dedede 55%, var(--silver) 100%);
    display: flex; align-items: center; justify-content: center;
  }
  .back-brand { display: flex; align-items: center; gap: 16px; }
  .back-brand .brand-square { width: 40px; height: 40px; background: var(--mid); }
  .back-brand .brand-name { font-size: 20px; letter-spacing: 2px; color: #7a7a7a; }
</style>
</head>
<body>

<section class="card card-front" aria-label="Business card front">
  <div class="front-band"></div>

  <div class="brand-mark">
    <span class="brand-square"></span>
    <span class="brand-name">Walsh &amp; Brand Pty Ltd.</span>
  </div>

  <div class="agent-block">
    <p class="agent-names">Owen Walsh &amp; Lucy Brand</p>
    <p class="agent-role">Sales Agents &amp; Onsite Manager</p>
  </div>
  <div class="rule rule-name"></div>

  <p class="address">3/42 Marlow Crescent,<br>FERNLEA QLD 4213</p>

  <div class="rule rule-contact"></div>
  <ul class="contact-list">
    <li><svg viewBox="0 0 12 12" aria-hidden="true"><path d="M2.5 1h2l1 2.5-1.3 1a6 6 0 0 0 3.3 3.3l1-1.3L11 7.5v2a1 1 0 0 1-1 1A9 9 0 0 1 1.5 2a1 1 0 0 1 1-1z"/></svg>07 5948 2063</li>
    <li><svg viewBox="0 0 12 12" aria-hidden="true"><path d="M3 1h5v3H3zM1 5h10v5H1zM3 8h6v3H3z"/></svg>07 5948 2174</li>
    <li><svg viewBox="0 0 12 12" aria-hidden="true"><path d="M3.5 0h5a1 1 0 0 1 1 1v10a1 1 0 0 1-1 1h-5a1 1 0 0 1-1-1V1a1 1 0 0 1 1-1zm.5 1.5v8h4v-8z"/></svg>0431 857 219</li>
  </ul>
</section>

<section class="card card-back" aria-label="Business card back">
  <div class="back-brand">
    <span class="brand-square"></span>
    <span class="brand-name">Walsh &amp; Brand Pty Ltd.</span>
  </div>
</section>

</body>
</html>
```